Oil Field Service company needs professional business cards

Looking to clean up our current company business cards and look a little more professional. Brenwick Casing Services is a US based company that services the oil field. We deal with engineers, managers and oil rigs....................................................................................................................................................................................................................................................................................................................................................................................................

Target Market(s)

Oil and Gas professionals

Industry/Entity Type

Oil And Gas

Contact Information for Business Card

See attached photo as example

Font styles to use
Sans Serif

Colors
ec1f27

Requirements
Must have
• Company Logo, Name, Title, Cell, Office, Fax, Email.
• See attached photo
Nice to have
• External CRT, Internal CRT, Casing Crews, Torque Turn, Laydown Machine
Should not have
• Do not introduce any new pictures and keep it professional looking

```html
<!DOCTYPE html>
<html lang="en">
<head>
<meta charset="utf-8">
<title>Brenwick Casing Services – Business Card</title>
<link rel="stylesheet" href="https://fonts.googleapis.com/css2?family=Open+Sans:wght@400;600;700;800&family=Roboto+Condensed:wght@700&display=swap">
<style>
  :root {
    --brand-red: #ec1f27;
    --deep-red: #c8161d;
    --charcoal: #2a2d31;
    --ink: #3a3d42;
    --text: #4a4d52;
    --mist: #d9dbde;
    --card: #fbfbfb;
    --backdrop: #e9eaec;
  }
  * { margin: 0; padding: 0; box-sizing: border-box; }
  html, body {
    width: 1200px; height: 969px; overflow: hidden;
    background: var(--backdrop);
    font-family: "Open Sans", Arial, sans-serif;
  }
  .business-card {
    position: absolute; left: 75px; top: 185px;
    width: 1050px; height: 600px;
    background: linear-gradient(180deg, #ffffff 0%, var(--card) 60%, #f1f2f3 100%);
    box-shadow: 0 10px 30px rgba(0,0,0,0.15);
    overflow: hidden;
  }
  .card-bands { position: absolute; inset: 0; }
  .company-name {
    position: absolute; left: 114px; top: 140px;
    color: var(--ink); font-weight: 800;
  }
  .company-name .wordmark { display: block; font-size: 74px; line-height: 1; letter-spacing: 1px; }
  .company-name .tagline {
    display: block; font-size: 21px; letter-spacing: 4.5px; margin-top: 18px; padding-left: 50px;
  }
  .service-list {
    position: absolute; left: 172px; top: 290px; list-style: none;
  }
  .service-list li {
    font-size: 27px; color: var(--text); height: 40px; line-height: 40px;
    display: flex; align-items: center;
  }
  .service-list li::before {
    content: ""; width: 9px; height: 9px; border-radius: 50%;
    background: var(--brand-red); margin-right: 14px;
  }
  .contact-block { position: absolute; left: 621px; top: 128px; }
  .person-name {
    font-family: "Roboto Condensed", Arial Narrow, sans-serif;
    font-weight: 700; font-size: 40px; color: var(--deep-red); line-height: 44px;
  }
  .person-title { font-size: 28px; font-weight: 700; color: var(--ink); line-height: 40px; letter-spacing: 0.5px; }
  .person-address { font-size: 26px; color: var(--text); margin-top: 16px; line-height: 34px; }
  .contact-list { list-style: none; margin-top: 22px; }
  .contact-list li {
    display: flex; align-items: center; height: 40px;
    font-size: 27px; color: var(--text);
  }
  .contact-list li.mobile { font-weight: 700; color: var(--ink); }
  .contact-list svg { width: 26px; height: 26px; margin-right: 20px; margin-left: 10px; fill: var(--deep-red); flex: none; }
</style>
</head>
<body>
  <div class="business-card">
    <svg class="card-bands" width="1050" height="600" viewBox="0 0 1050 600" aria-hidden="true">
      <path d="M0 0 H1050 V95 Q560 20 0 60 Z" fill="#e6e7e9"/>
      <path d="M0 0 H1050 V70 Q560 5 0 40 Z" fill="var(--brand-red)"/>
      <path d="M0 600 V500 Q540 575 1050 460 V600 Z" fill="var(--mist)"/>
      <path d="M0 600 V528 Q540 595 1050 495 V600 Z" fill="var(--charcoal)"/>
    </svg>

    <div class="company-name">
      <span class="wordmark">BRENWICK</span>
      <span class="tagline">CASING SERVICES</span>
    </div>

    <ul class="service-list">
      <li>External CRT</li>
      <li>Internal CRT</li>
      <li>Casing Crews</li>
      <li>Torque Turn</li>
      <li>Laydown Machine</li>
    </ul>

    <div class="contact-block">
      <div class="person-name">CODY HARLAN</div>
      <div class="person-title">AREA MANAGER</div>
      <div class="person-address">Redbank, OK 73590</div>
      <ul class="contact-list">
        <li class="office">
          <svg viewBox="0 0 24 24"><path d="M6.6 10.8a15.1 15.1 0 0 0 6.6 6.6l2.2-2.2a1 1 0 0 1 1-.25 11.4 11.4 0 0 0 3.6.57 1 1 0 0 1 1 1V20a1 1 0 0 1-1 1A17 17 0 0 1 3 4a1 1 0 0 1 1-1h3.5a1 1 0 0 1 1 1c0 1.25.2 2.45.57 3.57a1 1 0 0 1-.25 1z"/></svg>
          (555)210-4800
        </li>
        <li class="mobile">
          <svg viewBox="0 0 24 24"><path d="M7 1h10a2 2 0 0 1 2 2v18a2 2 0 0 1-2 2H7a2 2 0 0 1-2-2V3a2 2 0 0 1 2-2zm0 3v14h10V4zm5 15.5a1.2 1.2 0 1 0 0 2.4 1.2 1.2 0 0 0 0-2.4z"/></svg>
          (555)418-2093
        </li>
        <li class="fax">
          <svg viewBox="0 0 24 24"><path d="M7 2h10v5H7zM4 8h16a2 2 0 0 1 2 2v7h-3v5H5v-5H2v-7a2 2 0 0 1 2-2zm3 8v4h10v-4zm11-5.5a1 1 0 1 0 0 2 1 1 0 0 0 0-2z"/></svg>
          (555)210-4811
        </li>
        <li class="email">
          <svg viewBox="0 0 24 24"><path d="M2 5h20v14H2zm2 2v.5l8 5 8-5V7zm0 2.9V17h16V9.9l-8 5z"/></svg>
          cody@brenwick.com
        </li>
        <li class="web">
          <svg viewBox="0 0 24 24"><path d="M12 2a10 10 0 1 0 0 20 10 10 0 0 0 0-20zm6.9 6h-2.9a15 15 0 0 0-1.3-3.6A8 8 0 0 1 18.9 8zM12 4c.8 1.2 1.5 2.5 1.9 4h-3.8c.4-1.5 1.1-2.8 1.9-4zM4.3 14a8 8 0 0 1 0-4h3.3a16 16 0 0 0 0 4zm.8 2h2.9a15 15 0 0 0 1.3 3.6A8 8 0 0 1 5.1 16zM8 8H5.1a8 8 0 0 1 4.2-3.6A15 15 0 0 0 8 8zm4 12c-.8-1.2-1.5-2.5-1.9-4h3.8c-.4 1.5-1.1 2.8-1.9 4zm2.3-6H9.7a14 14 0 0 1 0-4h4.6a14 14 0 0 1 0 4zm.4 5.6A15 15 0 0 0 16 16h2.9a8 8 0 0 1-4.2 3.6zm1.7-5.6a16 16 0 0 0 0-4h3.3a8 8 0 0 1 0 4z"/></svg>
          www.brenwick.com
        </li>
      </ul>
    </div>
  </div>
</body>
</html>
```